Velk Partners Building Business Cards

We need a business card that reflects our business as "Solar Experts" in San Diego. Browse our website www.velkpartners.example our License needs to be displayed as "CSLB# 3867140" our phone number is (619) 555-0187

Save thousands on your electric bills and increase the value of your home while helping to protect the environment. Our solar installation experts will help you design the system that's right for you, using only the highest quality equipment that will look great and give you ideal performance. Our goal is to make you energy independent, and get your electric bill to 0.

Paul Osterby
(619) 555-0187
paul@velkpartners.example

Target Market(s)

Home owners in san diego looking for solar

Industry/Entity Type

Solar Energy

Contact Information for Business Card

Paul Osterby
(619) 555-0187
paul@velkpartners.example

Font styles to use
Other font styles liked:
• Use our logo font

Requirements
Must have
• License needs to be displayed as "CSLB# 3867140" our phone number is (619) 555-0187
Nice to have
• Real images of rooftop home solar in san diego
Should not have
• our business address

```html
<!DOCTYPE html>
<html lang="en">
<head>
<meta charset="utf-8">
<title>Velk Partners Building – Business Card</title>
<link href="https://fonts.googleapis.com/css2?family=Roboto:wght@400;500;700;900&display=swap" rel="stylesheet">
<style>
  :root {
    --navy: #27418a;
    --navy-deep: #1f3677;
    --gold: #eea812;
    --paper: #fbfbfb;
    --ink: #243a78;
    --backdrop: #a8a6a6;
    --faint: #ececec;
  }
  * { box-sizing: border-box; margin: 0; padding: 0; }
  html, body { width: 1200px; height: 1200px; overflow: hidden; }
  body {
    background: var(--backdrop);
    font-family: "Roboto", Arial, sans-serif;
    position: relative;
  }
  .card {
    position: absolute;
    border-radius: 28px;
    overflow: hidden;
  }
  /* Front */
  .card-front {
    left: 238px; top: 118px; width: 712px; height: 419px;
    background: var(--navy);
  }
  .front-photo {
    position: absolute; inset: 0;
    background: linear-gradient(160deg, #2d4a96 0%, #27418a 50%, #22397d 100%);
  }
  .brand-front {
    position: absolute; left: 0; right: 0; top: 58px;
    text-align: center;
    color: #fff; font-weight: 700; font-size: 50px; letter-spacing: -0.5px;
  }
  .process-title {
    position: absolute; left: 0; right: 0; top: 206px;
    display: flex; justify-content: center; align-items: center; gap: 26px;
    color: #fff; font-size: 22px; font-weight: 500; letter-spacing: 4px;
  }
  .process-title::before, .process-title::after {
    content: ""; width: 54px; height: 3px; background: var(--gold); border-radius: 2px;
  }
  .process-steps { position: absolute; left: 92px; top: 252px; width: 529px; height: 120px; }
  .step-link {
    position: absolute; top: 37px; height: 0;
    border-top: 2px dotted #fff;
  }
  .step { position: absolute; top: 0; width: 150px; text-align: center; }
  .step-icon {
    width: 77px; height: 77px; margin: 0 auto;
    background: var(--gold);
    display: flex; align-items: center; justify-content: center;
  }
  .step-label {
    margin-top: 8px; color: #fff; font-size: 13.5px; line-height: 15px;
  }
  /* Back */
  .card-back {
    left: 231px; top: 645px; width: 711px; height: 415px;
    background: var(--paper);
  }
  .sun-mark {
    position: absolute; left: 560px; top: 180px; width: 240px; height: 240px;
    border-radius: 50%; background: var(--faint);
  }
  .name-bar { position: absolute; left: 0; top: 33px; width: 19px; height: 69px; background: var(--gold); }
  .holder-name { position: absolute; left: 39px; top: 40px; color: var(--ink); font-size: 25px; font-weight: 700; letter-spacing: -0.3px; }
  .holder-title { position: absolute; left: 40px; top: 73px; color: var(--ink); font-size: 17px; }
  .brand-back {
    position: absolute; right: 28px; top: 46px;
    color: var(--ink); font-weight: 700; font-size: 33px; letter-spacing: -0.4px;
  }
  .contact-list { position: absolute; left: 40px; top: 305px; list-style: none; }
  .contact-list li {
    display: flex; align-items: center; gap: 16px;
    height: 25px; color: var(--ink); font-size: 18px;
  }
  .contact-list svg { width: 19px; height: 19px; flex: none; }
  .accent { color: var(--gold); }
  .license {
    position: absolute; left: 426px; top: 336px; width: 300px; height: 38px;
    background: var(--navy-deep);
    clip-path: polygon(14px 0, 100% 0, 100% 100%, 0 100%);
    color: #fff; font-size: 18px;
    display: flex; align-items: center; padding-left: 43px;
  }
</style>
</head>
<body>

<section class="card card-front">
  <div class="front-photo" role="img" aria-label="Faint photo of rooftop solar panels in blue tones"></div>
  <div class="brand-front">Velk Partners Building</div>
  <div class="process-title">OUR PROCESS</div>
  <div class="process-steps">
    <span class="step-link" style="left:77px;width:73px"></span>
    <span class="step-link" style="left:227px;width:73px"></span>
    <span class="step-link" style="left:377px;width:74px"></span>

    <div class="step" style="left:-37px">
      <div class="step-icon">
        <svg width="42" height="42" viewBox="0 0 42 42"><circle cx="17" cy="17" r="10" fill="none" stroke="#1f3677" stroke-width="4"/><line x1="24" y1="24" x2="36" y2="36" stroke="#1f3677" stroke-width="6" stroke-linecap="round"/></svg>
      </div>
      <p class="step-label">Site<br>Evaluation</p>
    </div>
    <div class="step" style="left:113px">
      <div class="step-icon">
        <svg width="42" height="42" viewBox="0 0 42 42"><path d="M10 6 L36 32 L38 40 L30 38 L4 12 Z" fill="none" stroke="#1f3677" stroke-width="3.5" stroke-linejoin="round"/><line x1="6" y1="16" x2="14" y2="8" stroke="#1f3677" stroke-width="3"/></svg>
      </div>
      <p class="step-label">Design &amp;<br>Permitting</p>
    </div>
    <div class="step" style="left:263px">
      <div class="step-icon">
        <svg width="44" height="36" viewBox="0 0 44 36"><rect x="6" y="2" width="32" height="20" rx="3" fill="#1f3677" transform="rotate(-10 22 12)"/><rect x="2" y="10" width="38" height="24" rx="3" fill="#1f3677" stroke="#eea812" stroke-width="2"/><rect x="2" y="15" width="38" height="5" fill="#eea812"/><rect x="28" y="25" width="8" height="4" fill="#eea812"/></svg>
      </div>
      <p class="step-label">Purchase of<br>Materials</p>
    </div>
    <div class="step" style="left:414px">
      <div class="step-icon">
        <svg width="46" height="46" viewBox="0 0 46 46"><line x1="8" y1="38" x2="36" y2="10" stroke="#1f3677" stroke-width="5" stroke-linecap="round"/><circle cx="36" cy="10" r="6" fill="none" stroke="#1f3677" stroke-width="4"/><line x1="10" y1="8" x2="38" y2="36" stroke="#1f3677" stroke-width="4" stroke-linecap="round"/><rect x="30" y="30" width="10" height="6" fill="#1f3677" transform="rotate(45 35 33)"/></svg>
      </div>
      <p class="step-label">Installation &amp;<br>Commissioning</p>
    </div>
  </div>
</section>

<section class="card card-back">
  <div class="sun-mark" aria-hidden="true"></div>
  <span class="name-bar"></span>
  <h1 class="holder-name">Paul Osterby</h1>
  <p class="holder-title">Managing Director</p>
  <div class="brand-back">Velk Partners Building</div>

  <ul class="contact-list">
    <li>
      <svg viewBox="0 0 20 20"><path d="M3 8 Q10 2 17 8 L15 10 L12 8 L8 8 L5 10 Z" fill="#eea812"/><rect x="5" y="10" width="10" height="7" rx="1" fill="#eea812"/></svg>
      (619) 555-0187
    </li>
    <li>
      <svg viewBox="0 0 20 20"><circle cx="10" cy="10" r="7.5" fill="none" stroke="#eea812" stroke-width="1.6"/><ellipse cx="10" cy="10" rx="3" ry="7.5" fill="none" stroke="#eea812" stroke-width="1.4"/><line x1="2.5" y1="10" x2="17.5" y2="10" stroke="#eea812" stroke-width="1.4"/></svg>
      paul@velkpartners.example
    </li>
    <li>
      <svg viewBox="0 0 20 20"><rect x="2" y="5" width="16" height="11" fill="#eea812"/><path d="M2 5 L10 12 L18 5" fill="none" stroke="#fbfbfb" stroke-width="1.5"/></svg>
      <span>www.<span class="accent">velkpartners</span>.example</span>
    </li>
  </ul>

  <div class="license">License: CSLB# 3867140</div>
</section>

</body>
</html>
```